Website for new dental office

I am Dr. Colin Ashford and am building a new dental practice. I specialize in general dentistry. I am young and have a higher end dental practice incorporating very new technologies and would like my website to reflect that. As many dental patients are older, the website must be very easy to navigate. I would like patients to be able to request appointments, and will eventually add on patient information forms (the health history, etc, that you normally fill out in the practice) from my practice management software, so leave an area for that.

Industry/Entity Type

Building

```html
<!DOCTYPE html>
<html lang="en">
<head>
<meta charset="utf-8">
<title>Colin Ashford, DDS</title>
<link href="https://fonts.googleapis.com/css2?family=Lato:wght@300;400;700&family=Open+Sans:wght@400;600;700&display=swap" rel="stylesheet">
<style>
:root{
  --cream:#fdf4ee;
  --teal:#0e8aa0;
  --teal-dark:#08778c;
  --orange:#f5821f;
  --tan:#cbb9a1;
  --green:#6cbd2c;
  --text:#555;
  --muted:#9a9a9a;
  --line:#eadfd6;
}
*{margin:0;padding:0;box-sizing:border-box}
html,body{width:976px;height:1200px;overflow:hidden;background:var(--cream)}
.page{position:relative;width:1200px;height:1475px;transform:scale(.81333);transform-origin:0 0;font-family:"Open Sans",sans-serif;color:var(--text)}
.abs{position:absolute}
.brand{font-family:"Lato",sans-serif;font-weight:700;color:var(--teal);font-size:32px;letter-spacing:.5px}
.phone{left:584px;top:16px;display:flex;align-items:center;gap:8px;font-size:21px;color:#444;font-family:"Lato",sans-serif}
.cta{left:809px;top:14px;width:281px;height:42px;background:var(--teal);color:#fff;font-family:"Lato",sans-serif;font-size:18px;display:flex;align-items:center;justify-content:center}
.nav a{position:absolute;top:75px;font-size:15px;color:#444;text-decoration:none}
.nav a.current{color:var(--teal)}
.hero{left:0;top:138px;width:1200px;height:336px;background:radial-gradient(circle at 200px 120px,#1a9bb0 0,#0f8aa0 40%,#0a7f95 70%,#0e8aa0 100%)}
.hero h1{position:absolute;left:110px;top:95px;font-family:"Lato",sans-serif;font-weight:700;font-size:43px;color:#fff;letter-spacing:-.5px}
.hero p{position:absolute;left:110px;top:146px;font-family:"Lato",sans-serif;font-size:28px;color:#fff;letter-spacing:1px}
.portrait{left:730px;top:108px;width:350px;height:302px;border-radius:120px 120px 0 0;background:linear-gradient(180deg,#e9c4a6 0,#f2f2f2 55%,#dfe7ee 100%)}
.appt-head{left:103px;top:410px;width:993px;height:64px;background:var(--orange);color:#fff;font-family:"Lato",sans-serif;font-size:30px;padding:14px 18px}
.appt-form{left:103px;top:474px;width:993px;height:115px;background:var(--tan)}
.appt-form .frame{position:absolute;left:7px;top:6px;width:979px;height:102px;border:2px solid #e3d7c8}
.field{position:absolute;top:37px;width:195px}
.field label{display:block;color:#fff;font-size:14px;margin-bottom:4px}
.field span{display:block;height:29px;background:#f9f1ea}
.send{position:absolute;left:844px;top:44px;width:110px;height:41px;background:linear-gradient(#86d13d,#5aab1f);border:1px solid #4f9a1a;color:#fff;font-weight:700;font-size:16px;display:flex;align-items:center;justify-content:center}
.about{left:102px;top:605px;width:994px;height:272px;background:#fff;border:1px solid var(--line)}
.about h2{position:absolute;left:27px;top:25px;font-size:26px;font-weight:700;color:var(--teal)}
.about .intro{position:absolute;left:27px;top:78px;width:228px;font-family:"Lato",sans-serif;font-size:13px;line-height:21px;color:var(--muted)}
.service{position:absolute;top:26px;width:210px}
.service .photo{height:111px;width:206px}
.service h3{font-size:18px;font-weight:600;color:var(--orange);margin:12px 0 10px 2px}
.service p{font-family:"Lato",sans-serif;font-size:13px;line-height:19px;color:var(--muted);margin-left:2px}
.arrow{position:absolute;top:725px;width:38px;height:38px}
.news-by{left:120px;top:918px;color:var(--teal);font-size:15px}
.news-title{left:120px;top:934px;color:var(--teal);font-size:26px;font-weight:700}
.rule{background:var(--line)}
.post{position:absolute}
.post .thumb{position:absolute;left:0;top:0}
.post h4{font-size:14px;font-weight:600;color:#333}
.post p{font-size:12.5px;line-height:16px;color:#444;margin-top:6px}
.post .more{font-size:11px;font-style:italic;color:#bbb;margin-top:8px;display:block}
.stories-title{left:764px;top:915px;color:var(--orange);font-size:24px;font-weight:600}
.story p{font-size:11px;line-height:15px}
.footer{left:0;top:1188px;width:1200px;height:287px;background:#fff}
.foot-col h5{font-size:18px;font-weight:400;color:#555;margin-bottom:22px}
.foot-col li{list-style:none;font-size:14px;line-height:22px;color:#666}
.foot-col li::before{content:"• ";font-size:10px;color:#999}
.address{font-size:14px;line-height:22px;color:#666}
.copyright{left:0;top:1447px;width:1200px;text-align:center;font-family:"Lato",sans-serif;font-size:13px;color:#333}
</style>
</head>
<body>
<div class="page">
  <header>
    <div class="abs brand" style="left:93px;top:48px">Colin Ashford, DDS</div>
    <div class="abs phone">
      <svg width="32" height="30" viewBox="0 0 32 30" aria-hidden="true"><path d="M6 4c2-2 4-1 5 1l2 4c1 2 0 3-1 4l-1 1c1 3 3 5 6 6l1-1c1-1 2-2 4-1l4 2c2 1 3 3 1 5l-2 2c-3 2-9 0-14-5S3 10 4 6z" fill="#444"/><rect x="14" y="0" width="16" height="11" rx="5" fill="none" stroke="#444" stroke-width="2"/></svg>
      <span>(123) 555-0148</span>
    </div>
    <div class="abs cta">Request a&nbsp;<b>FREE</b>&nbsp;Consultation</div>
    <nav class="nav">
      <a class="current" style="left:578px">HOME</a>
      <a style="left:657px">About Us</a>
      <a style="left:755px">Philosophy</a>
      <a style="left:865px">Tooth Replacement</a>
      <a style="left:1036px">Contact</a>
    </nav>
  </header>

  <section class="abs hero">
    <h1>I specialize in General Dentistry</h1>
    <p>Teeth Whitening Solutions for Everyone</p>
  </section>
  <div class="abs portrait" role="img" aria-label="Portrait of the dentist in a white coat"></div>

  <div class="abs appt-head">Make an Appointment</div>
  <form class="abs appt-form">
    <div class="frame"></div>
    <div class="field" style="left:19px"><label>Your Name:</label><span></span></div>
    <div class="field" style="left:219px"><label>Your Email:</label><span></span></div>
    <div class="field" style="left:420px"><label>Phone:</label><span></span></div>
    <div class="field" style="left:619px"><label>Appointment Date:</label><span></span></div>
    <div class="send">SEND</div>
  </form>

  <section class="abs about">
    <h2>ABOUT US</h2>
    <p class="intro">It is a long established fact that a reader will be distracted by the readable content of a page when looking at its layout. The point of using Lorem Ipsum is that it has a more-or-less normal distribution of letters, as opposed to using 'Content here, content here.</p>
    <div class="service" style="left:286px">
      <div class="photo" role="img" aria-label="Close-up of a bright smile" style="background:linear-gradient(135deg,#d8622c,#c83a2a 50%,#e8a07a)"></div>
      <h3>Cosmetics</h3>
      <p>It is a long established fact that a reader will be distracted by the readable content of a page when looking at its layout.</p>
    </div>
    <div class="service" style="left:511px">
      <div class="photo" role="img" aria-label="Patient during a dental examination" style="background:linear-gradient(135deg,#e9d6cc,#d7a99a 55%,#c7c9cc)"></div>
      <h3>Restorative</h3>
      <p>It is a long established fact that a reader will be distracted by the readable content of a page when looking at its layout.</p>
    </div>
    <div class="service" style="left:735px">
      <div class="photo" role="img" aria-label="Patient showing a restored tooth" style="background:linear-gradient(135deg,#b3a79c,#d6bfa8 55%,#7fb7bd)"></div>
      <h3>Tooth replacement</h3>
      <p>It is a long established fact that a reader will be distracted by the readable content of a page when looking at its layout.</p>
    </div>
  </section>
  <svg class="arrow" style="left:82px" viewBox="0 0 38 38" aria-hidden="true"><circle cx="19" cy="19" r="18" fill="#fff"/><circle cx="19" cy="19" r="15" fill="#bdbdbd"/><path d="M22 13l-7 6 7 6z" fill="#fff"/></svg>
  <svg class="arrow" style="left:1073px" viewBox="0 0 38 38" aria-hidden="true"><circle cx="19" cy="19" r="18" fill="#fff"/><circle cx="19" cy="19" r="15" fill="#bdbdbd"/><path d="M16 13l7 6-7 6z" fill="#fff"/></svg>

  <div class="abs news-by">Dr. Colin Ashford</div>
  <div class="abs news-title">Latest News</div>
  <div class="abs rule" style="left:112px;top:974px;width:592px;height:1px"></div>
  <article class="post" style="left:123px;top:1008px;width:570px">
    <div class="thumb" role="img" aria-label="Smiling patient" style="width:85px;height:93px;background:linear-gradient(160deg,#c9a27c,#e6c9b0 60%,#eee)"></div>
    <div style="margin-left:98px">
      <h4>Lorem Ipsum</h4>
      <p>It is a long established fact that a reader will be distracted by the readable content of a page when looking at its layout.The point of using Lorem Ipsum is that it has a more-or-less normal distribution of letters, as opposed to using 'Content here, content here', making it look like readable English.</p>
      <span class="more">Read More</span>
    </div>
  </article>

  <div class="abs rule" style="left:730px;top:925px;width:1px;height:243px"></div>
  <div class="abs stories-title">Patient Stories</div>
  <article class="post story" style="left:764px;top:958px;width:320px">
    <div class="thumb" role="img" aria-label="Dentist with a patient" style="width:81px;height:85px;background:linear-gradient(160deg,#ddd,#c9a88f 55%,#8a9aa8)"></div>
    <div style="margin-left:90px">
      <h4>Lorem Ipsum</h4>
      <p>It is a long established fact that a reader will be distracted by the readable content of a page when looking at its layout.</p>
      <span class="more">Read More</span>
    </div>
  </article>
  <article class="post story" style="left:764px;top:1067px;width:320px">
    <div class="thumb" role="img" aria-label="Smiling patient" style="width:81px;height:85px;background:linear-gradient(160deg,#c9a27c,#e6c9b0 60%,#eee)"></div>
    <div style="margin-left:90px">
      <h4>Lorem Ipsum</h4>
      <p>It is a long established fact that a reader will be distracted by the readable content of a page when looking at its layout.</p>
      <span class="more">Read More</span>
    </div>
  </article>

  <footer class="abs footer">
    <div class="abs foot-col" style="left:130px;top:26px">
      <h5>Quick Links</h5>
      <ul><li>About</li><li>Services</li><li>Resources</li><li>Case Studies</li><li>Blog</li><li>Locate Us</li><li>Contact</li></ul>
    </div>
    <div class="abs foot-col" style="left:327px;top:26px">
      <h5 style="margin-left:3px">Services</h5>
      <ul><li>Cosmetic</li><li>Restorative</li><li>Tooth Replacement</li></ul>
    </div>
    <div class="abs foot-col" style="left:557px;top:26px">
      <h5 style="margin-left:6px">Patient Info</h5>
      <ul><li>Mouth-Body Connection</li><li>Books &amp; Articles</li><li>FAQs</li><li>Helpful Links</li><li>Payment and Insurance</li><li>Pre &amp; Post Op Instructions</li></ul>
    </div>
    <div class="abs brand" style="left:823px;top:20px;font-size:26px">Colin Ashford, DDS</div>
    <div class="abs address" style="left:834px;top:70px">24 Harbor Lane<br>Suite 1 C/D<br>Loremipsum, LM 10019<br>Get Directions Tel: 123-555-0190</div>
    <div class="abs rule" style="left:110px;top:244px;width:980px;height:1px"></div>
  </footer>
  <div class="abs copyright">© Copyrights 2014 All rights Reserved</div>
</div>
</body>
</html>
```